Clearing Your Slate - Banner Ad for TH Website

I need a banner ad for a book I'm selling.

The book is about Clearing Your Slate, that is a County Court Judgment, from a credit report.

I have two websites. I want the banner ad to appear on
www.thorncaldwell.co.uk

It will then link to the new site: https://debtslatecleaner.co.uk/

The first site already has a lot of traffic from visitors wanting to remove a CCJ. The purpose of that first site was originally for visitors to become clients of the law firm. However, most visitors can't afford legal advice and so I'd like to offer them the book instead.

I would like to see designs that use the colour green. The final design should communicate financial freedom, simplicity and trustworthiness.

Target Market(s)

Individuals who have discovered a CCJ on their credit report

Industry/Entity Type

Law

Font styles to use
Sans Serif

Colors
0054AA
0677BA
7BADD7
CADEEF
E8F1F8
0094D4
00A9DD
6FCCEA
C7EBF8
E9F6FB
00AB8E
00BBA5
67D7C9
C6EFE9
E9F9F6

Requirements
Must have
• Must fit at the end of a blog article, such as this one https://www.thorncaldwell.co.uk/ccj-wrong-address/

```html
<!DOCTYPE html>
<html lang="en">
<head>
<meta charset="utf-8">
<title>Clearing Your Slate – Banner Set</title>
<link rel="stylesheet" href="https://fonts.googleapis.com/css2?family=Bebas+Neue&family=Montserrat:wght@500;800;900&display=swap">
<style>
:root{
  --teal-deep:#047a6b;
  --teal-mid:#00ab8e;
  --teal-soft:#67d7c9;
  --teal-pale:#c6efe9;
  --mint-wash:#e9f9f6;
  --ink:#111111;
  --white:#ffffff;
  --red-dark:#7e1f22;
  --red-bright:#d0202f;
  --display:"Montserrat",sans-serif;
  --condensed:"Bebas Neue",sans-serif;
}
*{box-sizing:border-box;margin:0;padding:0}
html,body{width:1042px;height:1200px;overflow:hidden;background:var(--white)}
.canvas{position:relative;width:1042px;height:1200px}

.banner{position:absolute;overflow:hidden}
.banner svg{position:absolute;left:0;top:0}
.cta{position:absolute;display:flex;align-items:center;justify-content:center;
  color:var(--white);font-family:var(--display);font-weight:500;letter-spacing:.04em;
  background:linear-gradient(90deg,var(--red-dark),var(--red-bright));text-decoration:none}
.tagline{position:absolute;font-family:var(--condensed);text-align:center;text-transform:uppercase;white-space:nowrap}
.title{position:absolute;font-family:var(--display);font-weight:900;text-transform:uppercase;line-height:.9;white-space:nowrap}
.title span{display:block}

/* Leaderboard */
.leaderboard{left:51px;top:36px;width:947px;height:122px;border:3px solid var(--teal-deep);background:var(--white)}
.leaderboard .title{left:39px;top:16px;color:var(--teal-deep)}
.leaderboard .title .l1{font-size:23px}
.leaderboard .title .l2{font-size:23px}
.leaderboard .title .l3{font-size:35px;letter-spacing:-.01em}
.leaderboard .tagline{left:170px;top:29px;width:230px;font-size:13.6px;line-height:19px;color:var(--ink);
  border-top:1.5px solid var(--teal-soft);border-bottom:1.5px solid var(--teal-soft);padding:5px 0}
.leaderboard .cta{left:828px;top:48px;width:91px;height:22px;border-radius:4px;font-size:10px}

/* Skyscraper */
.skyscraper{left:51px;top:203px;width:264px;height:972px;border:3px solid var(--teal-deep);background:var(--teal-soft)}
.skyscraper .title{left:0;width:258px;top:520px;text-align:center;color:var(--white);
  -webkit-text-stroke:2px var(--ink);paint-order:stroke fill}
.skyscraper .title .l1{font-size:33px}
.skyscraper .title .l2{font-size:44px}
.skyscraper .title .l3{font-size:56px}
.skyscraper .tagline{left:0;width:258px;top:692px;font-size:21px;line-height:28px;color:var(--ink)}
.skyscraper .cta{left:41px;top:863px;width:175px;height:43px;border-radius:9px;font-size:19px}

/* Rectangle */
.rectangle{left:416px;top:210px;width:587px;height:495px;border:9px solid var(--teal-deep);background:var(--mint-wash)}
.rectangle .tagline{left:362px;width:200px;top:62px;font-size:19.5px;line-height:26px;color:var(--white)}
.rectangle .title{left:357px;width:164px;top:266px;text-align:center;color:var(--teal-soft);
  -webkit-text-stroke:2px var(--ink);paint-order:stroke fill}
.rectangle .title .l1{font-size:25px}
.rectangle .title .l2{font-size:33px}
.rectangle .title .l3{font-size:42px}
.rectangle .cta{left:359px;top:393px;width:154px;height:38px;border-radius:9px;font-size:17px}
</style>
</head>
<body>
<main class="canvas">

  <section class="banner leaderboard" aria-label="Leaderboard banner">
    <svg width="941" height="116" viewBox="0 0 941 116">
      <defs>
        <linearGradient id="lb-wash" x1="0" x2="1">
          <stop offset="0" stop-color="#ffffff"/>
          <stop offset=".25" stop-color="#eef9f7"/>
          <stop offset="1" stop-color="#e4f5f2"/>
        </linearGradient>
        <linearGradient id="lb-cover" x1="0" y1="0" x2="1" y2="1">
          <stop offset="0" stop-color="#ffffff"/>
          <stop offset="1" stop-color="#d6f1ec"/>
        </linearGradient>
        <clipPath id="lb-clip"><polygon points="405,0 778,0 805,56 758,116 440,116"/></clipPath>
      </defs>
      <polygon points="405,0 778,0 805,56 758,116 440,116" fill="url(#lb-wash)"/>
      <g clip-path="url(#lb-clip)" role="img" aria-label="Row of Clearing Your Slate hardback books by Owen Hartley">
        <polygon points="418,10 470,2 498,120 446,126" fill="var(--teal-pale)"/>
        <polygon points="700,22 762,16 780,98 716,106" fill="var(--teal-pale)"/>
        <polygon points="704,18 760,12 776,92 718,100" fill="url(#lb-cover)" stroke="#bfe7e0"/>
        <polygon points="640,18 696,12 712,92 654,100" fill="var(--teal-pale)"/>
        <polygon points="636,14 692,8 708,88 650,96" fill="url(#lb-cover)" stroke="#bfe7e0"/>
        <polygon points="576,14 632,8 648,86 590,94" fill="var(--teal-pale)"/>
        <polygon points="572,10 628,4 644,82 586,90" fill="url(#lb-cover)" stroke="#bfe7e0"/>
        <polygon points="440,20 450,16 470,120 460,124" fill="var(--teal-soft)"/>
        <polygon points="450,16 556,4 588,112 470,124" fill="url(#lb-cover)" stroke="#bfe7e0"/>
      </g>
      <polyline points="778,0 805,56 758,116" fill="none" stroke="var(--teal-deep)" stroke-width="2"/>
      <polygon points="810,68 768,116 843,116" fill="var(--teal-deep)"/>
    </svg>
    <h2 class="title"><span class="l1">Clearing</span><span class="l2">Your</span><span class="l3">Slate</span></h2>
    <p class="tagline">We’ve helped people just like you by showing<br>them how to remove a county court judgement<br>from their credit record!</p>
    <a class="cta" href="https://debtslatecleaner.co.uk/">LEARN MORE</a>
  </section>

  <section class="banner skyscraper" aria-label="Skyscraper banner">
    <svg width="258" height="966" viewBox="0 0 258 966">
      <defs>
        <linearGradient id="sk-wash" x1="0" y1="0" x2="0" y2="1">
          <stop offset="0" stop-color="#ffffff"/>
          <stop offset="1" stop-color="#e4f6f3"/>
        </linearGradient>
        <linearGradient id="sk-cover" x1="0" y1="0" x2="1" y2="1">
          <stop offset="0" stop-color="#ffffff"/>
          <stop offset="1" stop-color="#d3f0eb"/>
        </linearGradient>
        <clipPath id="sk-clip"><path d="M0,0 H258 V290 L142,432 Q130,446 114,436 L0,350 Z"/></clipPath>
      </defs>
      <path d="M258,290 L165,408 Q140,440 160,455 L258,536 Z" fill="var(--teal-deep)"/>
      <path d="M0,0 H258 V290 L142,432 Q130,446 114,436 L0,350 Z" fill="url(#sk-wash)"/>
      <g clip-path="url(#sk-clip)" role="img" aria-label="Stack of Clearing Your Slate hardback books by Owen Hartley">
        <polygon points="18,40 140,18 150,40 30,62" fill="var(--teal-pale)"/>
        <polygon points="54,52 64,44 200,300 188,310" fill="var(--teal-soft)"/>
        <polygon points="64,44 240,14 280,260 200,300" fill="url(#sk-cover)" stroke="#bfe7e0"/>
        <polygon points="0,200 12,190 90,440 76,448" fill="var(--teal-soft)"/>
        <polygon points="0,190 12,190 90,440 0,420" fill="var(--teal-pale)"/>
        <polygon points="12,190 200,156 250,392 90,440" fill="url(#sk-cover)" stroke="#bfe7e0"/>
      </g>
      <path d="M0,350 L114,436 Q130,446 142,432 L258,290" fill="none" stroke="var(--ink)" stroke-width="4"/>
    </svg>
    <h2 class="title"><span class="l1">Clearing</span><span class="l2">Your</span><span class="l3">Slate</span></h2>
    <p class="tagline">We’ve helped people<br>just like you by showing<br>them how to remove a<br>county court judgement<br>from their credit record!</p>
    <a class="cta" href="https://debtslatecleaner.co.uk/">LEARN MORE</a>
  </section>

  <section class="banner rectangle" aria-label="Rectangle banner">
    <svg width="569" height="477" viewBox="0 0 569 477">
      <defs>
        <linearGradient id="rc-cover" x1="0" y1="0" x2="1" y2="1">
          <stop offset="0" stop-color="#ffffff"/>
          <stop offset="1" stop-color="#d3f0eb"/>
        </linearGradient>
      </defs>
      <circle cx="482" cy="83" r="176" fill="none" stroke="var(--teal-soft)" stroke-width="3"/>
      <circle cx="486" cy="79" r="170" fill="var(--teal-deep)"/>
      <g role="img" aria-label="Three Clearing Your Slate hardback books by Owen Hartley">
        <polygon points="80,300 380,250 372,280 90,332" fill="var(--teal-pale)"/>
        <polygon points="0,40 150,14 160,180 0,200" fill="url(#rc-cover)" stroke="#bfe7e0"/>
        <polygon points="80,50 92,40 170,300 156,310" fill="var(--teal-soft)"/>
        <polygon points="92,40 270,10 374,270 170,300" fill="url(#rc-cover)" stroke="#bfe7e0"/>
        <polygon points="60,440 280,400 290,420 70,462" fill="#9fded3"/>
        <polygon points="0,120 10,112 70,448 58,456" fill="var(--teal-soft)"/>
        <polygon points="10,112 200,90 282,396 70,448" fill="url(#rc-cover)" stroke="#bfe7e0"/>
      </g>
    </svg>
    <p class="tagline">We’ve helped people<br>just like you by showing<br>them how to remove a<br>county court judgement<br>from their credit record!</p>
    <h2 class="title"><span class="l1">Clearing</span><span class="l2">Your</span><span class="l3">Slate</span></h2>
    <a class="cta" href="https://debtslatecleaner.co.uk/">LEARN MORE</a>
  </section>

</main>
</body>
</html>
```